Letter design, envelope design, and more

Hello, we the Tavrin Gmbh are looking for our shop. Letter C5. Design does not have to be like a business card, so it can have straight lines. Only the color is important. The logo is the text under TaVRin omit.It should not be playful but Profesionel

Font styles to use
Sans Serif

Colors
0555a3
3176b5
85abd2
85cae6
34a7d8
0792cd
cee9f5
cfdfed
000000

Requirements
Must have
• Color like business card, Please, with the text under TaVRin, Correct address Lindmattstr. 4 Zip code 9517 Rorwil, as well as Couvert Without addressing only design and logo with TaVrn
Nice to have
• more writing articles
Should not have
• Not too colored, Text under TaVRin, bright colors

```html
<!DOCTYPE html>
<html lang="en">
<head>
<meta charset="utf-8">
<title>Tavrin Gmbh – Stationery</title>
<link rel="stylesheet" href="https://fonts.googleapis.com/css2?family=Raleway:wght@400;700&family=Roboto:wght@400&display=swap">
<style>
  :root{
    --navy:#00215a;
    --grey:#8a909d;
    --paper:#f7f7f7;
    --ground:#e0e0e0;
    --ink:#444a55;
    --rule:#6d7fb5;
  }
  *{margin:0;padding:0;box-sizing:border-box}
  html,body{width:1200px;height:877px;overflow:hidden;background:var(--ground)}
  body{position:relative;font-family:"Raleway",sans-serif;color:var(--ink)}
  .sheet{position:absolute;background:var(--paper);overflow:hidden}
  .sheet svg.bands{position:absolute;inset:0;width:100%;height:100%}
  .letter{left:69px;top:64px;width:528px;height:742px}
  .envelope-back{left:614px;top:269px;width:531px;height:240px}
  .envelope-front{left:614px;top:562px;width:532px;height:241px}

  .wordmark{position:absolute;display:flex;align-items:center;gap:7px;
    font-family:"Raleway",sans-serif;font-weight:700;color:var(--navy);letter-spacing:1px}
  .wordmark .mark{display:block;background:var(--navy)}
  .letter .wordmark{left:0;right:0;top:50px;justify-content:center;font-size:26px}
  .letter .wordmark .mark{width:30px;height:30px}
  .envelope-front .wordmark{left:28px;top:41px;font-size:22px}
  .envelope-front .wordmark .mark{width:26px;height:26px}
  .envelope-back .wordmark{left:0;right:0;top:24px;justify-content:center;font-size:22px;color:#fff}

  .salutation{position:absolute;left:45px;top:212px;font-size:13.5px;color:#3c4250}
  .body-copy{position:absolute;left:45px;top:250px;width:438px;font-size:7.6px;line-height:11.3px;text-align:justify;color:#3f4552}
  .body-copy p{margin-bottom:11.3px}
  .closing{position:absolute;left:45px;top:489px;font-size:7.6px}
  .signature{position:absolute;left:41px;top:520px;width:94px;height:38px;background:linear-gradient(90deg,rgba(31,79,160,.25),rgba(31,79,160,.12));border-radius:4px}

  .contacts{position:absolute;left:25px;top:674px;list-style:none;font-family:"Roboto",sans-serif;font-size:7.6px;line-height:10.4px;color:#3c4250}
  .contacts li{display:flex;align-items:center;gap:5px}
  .contacts svg{width:7px;height:7px;fill:var(--navy)}
  .address{position:absolute;right:29px;top:687px;font-family:"Roboto",sans-serif;font-size:7.6px;color:#3c4250}
  .footer-rule{position:absolute;left:94px;right:29px;top:702px;height:1px;background:var(--rule)}
</style>
</head>
<body>

<section class="sheet letter" aria-label="Letterhead">
  <svg class="bands" viewBox="0 0 528 742" preserveAspectRatio="none" aria-hidden="true">
    <polygon points="0,0 528,0 528,4 0,20" fill="var(--grey)"/>
    <polygon points="0,742 528,720 528,742" fill="var(--navy)"/>
  </svg>
  <div class="wordmark"><span class="mark"></span>TaVRin</div>

  <p class="salutation">Dear Mr. Keller,</p>
  <div class="body-copy">
    <p>Lorem ipsum dolor sit amet, consectetur adipiscing elit. Donec orci purus, luctus vitae dignissim eu, iaculis sed purus. Vivamus faucibus, ipsum nec aliquet viverra, leo mauris condimentum ligula, sit amet sagittis enim ligula quis arcu. Nam egestas tortor id nisi porttitor mattis. In tortor ante, ultricies in suscipit a, tempus non massa. Vivamus et auctor mi. Fusce vel massa nulla. Phasellus nec eros mauris, et scelerisque orci.</p>
    <p>Donec malesuada orci vitae nulla accumsan porta a id massa. Quisque accumsan iaculis magna sit amet fringilla. Maecenas consequat, magna eget tincidunt semper, odio nibh rutrum mi, id feugiat ante nisi eu risus. Vestibulum nunc orci, rhoncus a placerat in, ultricies in mi. Cras mattis varius eros, vel fringilla nisi suscipit eget. Quisque scelerisque sagittis nulla at porttitor.</p>
    <p>Sed id augue vitae urna euismod commodo aliquet a quam. Pellentesque arcu velit, cursus et malesuada ut, consequat et diam. Nullam erat sem, rhoncus id ullamcorper vitae, rhoncus et arcu. In ultricies ultricies nulla, ut rutrum nisi iaculis at. Donec eu magna a metus ornare faucibus. Fusce aliquet faucibus ultricies. Morbi semper, est id tincidunt gravida, sem arcu adipiscing lacus, ac bibendum nulla leo eu purus. Quisque nec diam sed risus consectetur a ccumsan quis quis nibh. Vestibulum id purus lorem.</p>
    <p>It is a long established fact that a reader will be distracted by the readable content of a page when looking at its layout. The point of using Lorem Ipsum is that it has a more-or-less normal distribution of letters, as opposed to using 'Content here, content here', making it look like readable English. Many desktop publishing packages</p>
  </div>
  <p class="closing">Sincerely,</p>
  <div class="signature" role="img" aria-label="Handwritten signature of Lukas Keller"></div>

  <ul class="contacts">
    <li><svg viewBox="0 0 10 10"><path d="M2 0h2l1 3-1.5 1a6 6 0 0 0 2.5 2.5L7 5l3 1v2c0 1-1 2-2 2A8 8 0 0 1 0 2c0-1 1-2 2-2z"/></svg>+41 71 555 02 40</li>
    <li><svg viewBox="0 0 10 10"><path d="M0 2h10v1L5 6 0 3zM0 4l5 3 5-3v4H0z"/></svg>info@tavrin.ch</li>
    <li><svg viewBox="0 0 10 10"><circle cx="5" cy="5" r="5"/></svg>www.tavrin.ch</li>
  </ul>
  <p class="address">Lindmattstr. 4, 9517 Rorwil</p>
  <div class="footer-rule"></div>
</section>

<section class="sheet envelope-back" aria-label="Envelope back">
  <svg class="bands" viewBox="0 0 531 240" preserveAspectRatio="none" aria-hidden="true">
    <path d="M0,0 H531 L524,38 Q518,73 490,73 H41 Q13,73 7,38 Z" fill="var(--navy)"/>
  </svg>
  <div class="wordmark">TaVrn</div>
</section>

<section class="sheet envelope-front" aria-label="Envelope front">
  <svg class="bands" viewBox="0 0 532 241" preserveAspectRatio="none" aria-hidden="true">
    <polygon points="0,0 532,0 532,4 0,19" fill="var(--grey)"/>
    <polygon points="0,241 532,222 532,241" fill="var(--navy)"/>
  </svg>
  <div class="wordmark"><span class="mark"></span>TaVrn</div>
</section>

</body>
</html>
```